Visitenkarten-Design für  Softwareunternehmen
Visitenkarten-Design für Softwareunternehmen
Zielgruppe
Wir sind ein B2B Softwareunternehmen, das eine Energiemonitoringsoftware für die mittelständische Industrie entwickelt hat. Das heißt unsere Visitenkarten werden überwiegend an unsere Zielgruppe, d.h. Geschäftsführer produzierender mittelständischer Industrie ausgehändigt.
Aufgabenstellung
Gleichzeitig treten wir nach außen jung, innovativ und voller Tatendrang auf. Ganz nach unserer Vision: Voll Energie. Null Emission. (Auch gerne auf der Visitenkarte mit aufnehmen). Uns ist es wichtig, unser CI nach außen zu kommunizieren und unsere Webseite auf der Visitenkarte zu platzieren.
Die Visitenkarte soll einzeln für jeden MitarbeiterIn personalisiert werden können.

```html
<!DOCTYPE html>
<html lang="de">
<head>
<meta charset="utf-8">
<title>Visitenkarte VOLTAN</title>
<link rel="stylesheet" href="https://fonts.googleapis.com/css2?family=Montserrat:wght@300;400;700&display=swap">
<style>
  :root {
    --ink: #263031;
    --paper: #ffffff;
    --stage: #f4f4f4;
  }
  * { box-sizing: border-box; margin: 0; padding: 0; }
  html, body { width: 1200px; height: 1200px; overflow: hidden; }
  body {
    background: var(--stage);
    font-family: "Montserrat", sans-serif;
    color: var(--ink);
    position: relative;
  }
  .card {
    position: absolute;
    left: 218px;
    width: 764px;
    height: 438px;
  }
  .card--front { top: 138px; background: var(--paper); box-shadow: 0 0 0 1px #e6e6e6; }
  .card--back { top: 625px; background: var(--ink); }

  .brand {
    position: absolute;
    left: 0; right: 0;
    text-align: center;
    font-weight: 700;
    letter-spacing: 0.12em;
    line-height: 1;
  }
  .card--front .brand { top: 98px; font-size: 72px; color: var(--ink); }
  .card--back .brand { top: 160px; font-size: 110px; color: var(--paper); }

  .contact {
    position: absolute;
    left: 40px;
    top: 270px;
    list-style: none;
    font-size: 18px;
    font-weight: 400;
  }
  .contact li {
    display: flex;
    align-items: center;
    height: 31px;
  }
  .contact .icon {
    width: 28px;
    flex: 0 0 28px;
    display: flex;
    align-items: center;
  }
  .contact svg { width: 18px; height: 18px; }

  .divider {
    position: absolute;
    left: 382px;
    top: 250px;
    width: 2px;
    height: 156px;
    background: var(--ink);
  }
  .person {
    position: absolute;
    left: 441px;
    top: 299px;
    font-size: 38px;
    font-weight: 300;
  }
</style>
</head>
<body>
  <section class="card card--front">
    <div class="brand">VOLTAN</div>
    <ul class="contact">
      <li>
        <span class="icon"><svg viewBox="0 0 24 24" fill="none" stroke="currentColor" stroke-width="2"><path d="M12 22s7-7 7-12a7 7 0 0 0-14 0c0 5 7 12 7 12z"/><circle cx="12" cy="10" r="2.5"/></svg></span>
        Lindenweg 8, 54321 Musterstadt
      </li>
      <li>
        <span class="icon"><svg viewBox="0 0 24 24" fill="none" stroke="currentColor" stroke-width="2"><rect x="3" y="5" width="18" height="14"/><path d="M3 6l9 7 9-7"/></svg></span>
        marenholtkamp@voltan.de
      </li>
      <li>
        <span class="icon"><svg viewBox="0 0 24 24" fill="none" stroke="currentColor" stroke-width="2"><path d="M5 3h4l2 5-3 2a11 11 0 0 0 6 6l2-3 5 2v4a2 2 0 0 1-2 2A17 17 0 0 1 3 5a2 2 0 0 1 2-2z"/></svg></span>
        015120450078
      </li>
      <li>
        <span class="icon"></span>
        06541/208-419
      </li>
    </ul>
    <div class="divider"></div>
    <div class="person">marenholtkamp</div>
  </section>

  <section class="card card--back">
    <div class="brand">VOLTAN</div>
  </section>
</body>
</html>
```